Exciting adult social quiz app needs awesome modern design

A new and exciting app for couples/sexual partners is in the making. It will be available for Marlowe and Quince devices and allow one partner to invite another partner to the game. The partners will answer questions about their sexual desires and needs and then try to guess what the other one answered.

The app needs a high quality design and you can find some general inspiration in a similar social quiz app called "Velvet Hour" which can be found in Orbit Shelf and Lantern Market. I like some of the basic layouts of this app.

The design should be classy and have a theme that matches the app subject. This is a sexual get-to-know-each-other-app and not a "porn app". I imagine colors might be black and red (not a requirement) and perhaps have some structures, pictures or backgrounds showing a bit of skin. It's important that the game can be accessed by players in the public space (e.g. in a bus, car etc.) without surroundings thinking it's a sex/porn game - but also important that it's exciting in a kind of sexual way. So try to find a fine line.

As the app is for both genders, the design should accommodate this.

Please see app mockups in the attached PDF.

Initially, please show design proposals for screens 13, 16 and 23.
Please notice that screen 16 doesn't have to be exactly those 2 bars - please make some alternative score comparison graphic in your proposal.

Looking forward to seeing your proposal soon!

Target Market(s)

Couples between 18 and 50

Industry/Entity Type

Adult

Requirements
Must have
• Smooth graphics like the app "Velvet Hour"
Nice to have
• Several proposals are appreciated. Perhaps you can show your proposals with different colors and object placements so that I can see some different options.

```html
<!DOCTYPE html>
<html lang="en">
<head>
<meta charset="utf-8">
<title>Waiting for your turn</title>
<link href="https://fonts.googleapis.com/css2?family=Ubuntu:wght@700&display=swap" rel="stylesheet">
<style>
  :root {
    --header-red: #7d0000;
    --bg-deep: #6e2526;
    --bg-mid: #a83c3e;
    --bg-soft: #b84e4e;
    --button-top: #a8050a;
    --button-bottom: #6f0004;
    --ring-red: #a10d0f;
    --symbol-red: #8a0a0c;
    --gold-line: #c9a85a;
    --title-top: #ffffff;
    --title-bottom: #e6e23a;
    --outline-dark: #2a0000;
    --bubble: #e6c9c9;
    --bubble-text: #1c1414;
    --input-bg: #a88283;
    --input-text: #8a5a5b;
    --ads-blue: #0000ff;
    --white: #ffffff;
    --avatar-fill: #6b5552;
  }
  * { margin: 0; padding: 0; box-sizing: border-box; }
  html, body { width: 700px; height: 1200px; overflow: hidden; background: var(--bg-deep); }
  body { font-family: "Ubuntu", "Arial Black", sans-serif; font-weight: 700; }
  .screen { position: relative; width: 700px; height: 1200px; overflow: hidden; }
  .backdrop {
    position: absolute; inset: 0;
    background:
      radial-gradient(ellipse 420px 520px at 360px 560px, var(--bg-soft), transparent 70%),
      radial-gradient(ellipse 300px 400px at 600px 300px, #a84848, transparent 70%),
      linear-gradient(180deg, var(--bg-mid), var(--bg-deep));
  }
  .header {
    position: absolute; left: 0; top: 0; width: 700px; height: 130px;
    background: var(--header-red);
    display: flex; align-items: center; justify-content: center;
  }
  .title-text {
    font-size: 56px; line-height: 1; white-space: nowrap;
    background: linear-gradient(180deg, var(--title-top) 15%, var(--title-bottom) 85%);
    -webkit-background-clip: text; background-clip: text; -webkit-text-fill-color: transparent;
    filter: drop-shadow(4px 0 0 var(--outline-dark)) drop-shadow(-4px 0 0 var(--outline-dark))
            drop-shadow(0 4px 0 var(--outline-dark)) drop-shadow(0 -4px 0 var(--outline-dark));
  }
  .header .title-text { font-size: 57px; letter-spacing: 0.5px; }
  .divider { position: absolute; left: 80px; width: 540px; height: 3px;
    background: linear-gradient(90deg, transparent, var(--gold-line) 15%, var(--gold-line) 85%, transparent); }
  .divider-top { top: 133px; }
  .divider-chat { top: 460px; }
  .section-label { position: absolute; left: 0; width: 700px; top: 430px; text-align: center; }
  .section-label .title-text { font-size: 54px; display: inline-block; padding: 0 8px; }
  .player-name { position: absolute; left: 83px; top: 154px; color: var(--white); font-size: 31px; line-height: 1; }
  .nudge-button {
    position: absolute; left: 140px; top: 183px; width: 480px; height: 192px;
    border: none; font-family: inherit; font-weight: 700;
    background: linear-gradient(180deg, var(--button-top), var(--button-bottom));
    box-shadow: 4px 6px 10px rgba(0,0,0,.45);
    display: flex; align-items: center; justify-content: center; padding-left: 20px;
    color: var(--white); font-size: 54px; line-height: 1;
    text-shadow: 2px 3px 4px rgba(0,0,0,.4);
  }
  .symbol { position: absolute; overflow: visible; }
  .avatar-photo { fill: var(--avatar-fill); }
  .bubble {
    position: absolute; background: var(--bubble); color: var(--bubble-text);
    display: flex; align-items: center; height: 66px; border-radius: 33px;
    font-size: 32px; line-height: 1; white-space: nowrap;
  }
  .bubble-incoming { left: 178px; top: 551px; width: 467px; border-top-left-radius: 6px; padding-left: 57px; }
  .bubble-outgoing { left: 272px; top: 717px; width: 233px; border-top-right-radius: 6px; padding-left: 14px; }
  .chat-input {
    position: absolute; left: 30px; top: 1020px; width: 642px; height: 86px;
    background: var(--input-bg); border: 6px solid #5a2324; border-right-color: #8a5a5a; border-bottom-color: #8a5a5a;
    color: var(--input-text); font-size: 32px; display: flex; align-items: center; padding-left: 22px;
  }
  .ad-slot {
    position: absolute; left: 110px; top: 1134px; width: 491px; height: 66px;
    background: var(--ads-blue); color: var(--white); font-size: 36px;
    display: flex; align-items: center; justify-content: center;
  }
</style>
</head>
<body>
<main class="screen">
  <div class="backdrop" role="img" aria-label="Blurred warm-toned photo of skin as background"></div>

  <header class="header"><h1 class="title-text">Waiting for your turn</h1></header>
  <div class="divider divider-top"></div>

  <div class="player-name">Mira</div>
  <button class="nudge-button" type="button">Send nudge</button>

  <div class="divider divider-chat"></div>
  <div class="section-label"><h2 class="title-text">Chat</h2></div>

  <div class="bubble bubble-incoming">We can chat here!</div>
  <div class="bubble bubble-outgoing">Cool!</div>

  <svg class="symbol" style="left:0;top:0" width="700" height="1200" viewBox="0 0 700 1200">
    <g stroke="var(--symbol-red)" stroke-width="12" fill="none">
      <line x1="125" y1="305" x2="125" y2="418"/>
      <line x1="88" y1="352" x2="178" y2="352"/>
    </g>
    <circle cx="125" cy="255" r="58" fill="var(--ring-red)"/>
    <circle class="avatar-photo" cx="125" cy="255" r="47" role="img" aria-label="Profile photo of Mira"/>

    <g stroke="var(--symbol-red)" stroke-width="10" fill="none">
      <line x1="97" y1="620" x2="97" y2="705"/>
      <line x1="63" y1="655" x2="130" y2="655"/>
    </g>
    <circle cx="97" cy="580" r="48" fill="var(--ring-red)"/>
    <circle class="avatar-photo" cx="97" cy="580" r="38" role="img" aria-label="Profile photo of Mira"/>
    <path d="M148 552 L200 552 L190 568 Z" fill="var(--bubble)"/>

    <g stroke="var(--ring-red)" stroke-width="11" fill="none" stroke-linecap="square">
      <line x1="605" y1="725" x2="686" y2="682"/>
      <polyline points="645,677 688,681 678,722"/>
    </g>
    <circle cx="568" cy="752" r="48" fill="var(--ring-red)"/>
    <circle class="avatar-photo" cx="568" cy="752" r="38" fill="#7b7565" role="img" aria-label="Profile photo of the player"/>
    <path d="M522 717 L480 717 L500 734 Z" fill="var(--bubble)"/>
  </svg>

  <div class="chat-input">Chat text here</div>
  <div class="ad-slot">Ads here</div>
</main>
</body>
</html>
```